Wordpress Design Project - Australian Solar Company wants to start FRESH!

About us

Bright Meadow are a renewable energy company based in Perth Australia, but we also have offices all over Asia. We specialise in offering renewable energy solutions (Solar PV Systems and LED Lighting) to residential and commercial customers.

Our current website: www.brightmeadowenergy.com.au

Our needs

This will be a replacement website as we are not happy with our current layout. We have an Australian company doing our SEO and they have recommended a new layout which we wish to go with.

We really want a professional and easy to navigate website that will assist in bringing in more enquiries and phone calls.

Content

We have all the content and will get the design winner to add this after we have chosen the design we like.
It is important that the call to actions are presented well and are visible these are things like the free quote form and our phone number.

The layout as we have advised has been based on SEO research so we wish it to be exactly the same unless otherwise stated.

Call to action

Our main objective of the new website is for people to come to the home page and see us as a professional and reliable company to deal with and enquire further.

We really want as many people as we can to convert to a lead. We want every person that comes to the website to enquire online or call us. We feel it is important to have a contact us/quote form on every page of the website.

Functional requirements

We have a chatterbook and vidstream account so links to these would be needed

Design assets

The logo needs to be displayed as shown in the website layout brief

Colours – we would like fresh, subdued colours that are professional and appealing to the eye. We ask that you do not take the colours from the logo.

Current website dislikes – the things we currently dislike about our current website is that it is hard to find information and there is no clear call to action. The colours are really unappealing as well as it looks cheap not professional.
The graphics that we require for the slider on the home page will have to be given after the winner is chosen but we want there to be three sliders on rotation

- Credibility builder (employee infront of solar panel) that encourages we use all our own employees not subcontractors
- Residential Slider – picture of a couple and solar panel system with a testimonial
- Commercial slider – picture of commercial system with “find out how you can install solar for free* at your business”

Design ideas

The website needs to be mobile friendly as well
It is going to be a total rebuild from the current website as our current website really isn’t working for us.

Target Market(s)

Target Audience

Our target audience are both residential and commercial clients
Residential – we want to attract home owners that are interested in reducing their electricity bill and helping the environment. Generally these people are between the ages of 28-50+ both male and female.

Commercial – We want to appeal to key decision makers within the commercial sphere. For example – CEOs, Company Directors, Operation managers and business owners of any industry. These people will be interested in reducing their electricity bills and creating a clean green image for their business.
Our target audience will generally come to our website to get information and enquire for a quote/ product information.

Industry/Entity Type

Residential

Requirements
Must have
• MUST BE LAID OUT LIKE THIS:

http://www.pagevaultdocs.com/doc/482937105/Website-Layout

Must have Enquire Now forms on every page that read:

Name
Phone Number
How did you hear about us
Message

```html
<!DOCTYPE html>
<html lang="en">
<head>
<meta charset="utf-8">
<title>Bright Meadow – Home</title>
<link href="https://fonts.googleapis.com/css2?family=PT+Sans:wght@400;700&display=swap" rel="stylesheet">
<style>
:root{
  --green:#1a8a3a;
  --green-dark:#0f6a2a;
  --green-deep:#0a4a1f;
  --orange:#f39a12;
  --orange-light:#fbc045;
  --ink:#3a3a3a;
  --muted:#6a6a6a;
  --sky-top:#1b5fbf;
  --sky-bottom:#7bb3ea;
  --form-head:#0b2e22;
  --white:#ffffff;
}
*{box-sizing:border-box;margin:0;padding:0}
html,body{width:910px;height:1200px;overflow:hidden;background:var(--white)}
body{position:relative;font-family:"PT Sans",sans-serif;color:var(--ink)}
.abs{position:absolute}
.top-rule{left:0;top:0;width:910px;height:3px;background:var(--green)}

/* header */
.brand{left:78px;top:40px;display:flex;align-items:center;gap:10px}
.brand-mark{width:46px;height:46px;border-radius:50%;background:var(--orange)}
.brand-name{font-size:26px;font-weight:700;color:var(--green)}
.call{left:647px;top:24px;color:var(--green)}
.call-label{font-size:15px;line-height:17px}
.call-number{font-size:20px;line-height:22px;color:var(--green-dark)}
.socials{left:767px;top:42px;display:flex;gap:4px}
.socials span{width:18px;height:17px;border-radius:3px;background:#3b7bd0}
.socials span:nth-child(2){background:#1f6aa6}
.socials span:nth-child(3){background:#3b5a9a}
.nav{left:295px;top:72px;width:541px;height:41px;border-radius:4px;
  background:linear-gradient(#fbbf3e,#f19a0e);display:flex;align-items:center;justify-content:center;
  box-shadow:0 1px 2px rgba(0,0,0,.25)}
.nav a{color:var(--white);text-decoration:none;font-size:14px;padding:0 11px;border-left:1px solid rgba(255,255,255,.55);line-height:15px}
.nav a:first-child{border-left:none}

/* hero */
.hero{left:0;top:123px;width:910px;height:330px;
  background:linear-gradient(160deg,var(--sky-top) 0%,#3f86d8 45%,var(--sky-bottom) 100%)}
.hero-panels{left:300px;top:123px;width:610px;height:330px;
  background:linear-gradient(200deg,#0d2f7a 0%,#1c4aa8 50%,#0b2460 100%);
  clip-path:polygon(35% 100%,62% 20%,100% 0,100% 100%)}
.hero-title{left:87px;top:188px;font-size:40px;font-weight:700;color:var(--white);letter-spacing:.3px}
.hero-text{left:89px;top:238px;width:290px;font-size:11.5px;line-height:18px;color:var(--white)}
.btn-learn{left:88px;top:299px;width:77px;height:25px;border-radius:3px;background:linear-gradient(#2f8be0,#1566c4);
  color:var(--white);font-size:10.5px;line-height:25px;text-align:center;box-shadow:0 1px 2px rgba(0,0,0,.3)}
.dots{left:92px;top:341px;display:flex;gap:3px}
.dots span{width:9px;height:9px;border-radius:50%;background:rgba(255,255,255,.45)}
.dots span:first-child{background:var(--white)}

/* enquiry form */
.enquiry{left:609px;top:144px;width:216px;height:251px;background:rgba(18,96,48,.88)}
.enquiry-head{height:38px;background:var(--form-head);color:var(--white);font-size:18px;line-height:38px;padding-left:17px}
.field{position:absolute;left:13px;width:189px;height:24px;background:var(--white);border:1px solid #cfd6d1;border-radius:2px;
  font-size:9px;color:#666;padding:6px 10px}
.btn-orange{position:absolute;background:linear-gradient(#fbbf3e,#f1940c);color:var(--white);text-align:center;border-radius:2px}

/* service cards */
.card{top:421px;width:180px;height:214px;background:linear-gradient(#ffffff 40%,#efefef);border:1px solid #e0e0e0;border-radius:3px;text-align:center}
.card h3{margin-top:20px;font-size:19.5px;line-height:23px;font-weight:400;color:var(--green)}
.card p{margin:11px auto 0;width:150px;font-size:10.5px;line-height:16.5px;color:var(--muted)}
.btn-green{display:block;margin:12px auto 0;width:71px;height:23px;background:linear-gradient(#1f9a42,#0e6d2a);
  color:var(--white);font-size:8.5px;line-height:23px;border-radius:2px}

/* welcome */
.welcome-title{left:77px;top:683px;font-size:21px;color:#333}
.welcome-lead{left:79px;top:714px;font-size:12px;color:#444}
.welcome-text{left:79px;top:739px;width:430px;font-size:9.5px;line-height:18px;color:var(--muted)}
.photo{background:linear-gradient(160deg,#8fb6df 0%,#3f6ea8 45%,#c7ccd2 100%)}
.benefits{left:271px;top:787px}
.benefits h4{font-size:12px;font-weight:400;color:#444;margin-bottom:6px}
.benefits li{list-style:none;font-size:10px;color:#555;line-height:22px;padding-left:11px;position:relative}
.benefits li::before,.foot-list li::before{content:"";position:absolute;left:1px;top:50%;margin-top:-4px;border-left:4px solid currentColor;border-top:4px solid transparent;border-bottom:4px solid transparent}
.testimonials-title{left:529px;top:683px;font-size:21px;color:var(--orange)}
.video{left:531px;top:714px;width:297px;height:184px;background:linear-gradient(160deg,#a9c3dc 0%,#e8ecef 45%,#6f7a84 100%)}
.play{left:662px;top:789px}

/* footer */
.footer{left:0;top:947px;width:910px;height:253px;background:linear-gradient(#1c8e45,#0f6a2e 70%,#0c5a27)}
.foot-head{top:979px;font-size:16px;color:var(--white)}
.foot-rule{top:980px;width:1px;height:138px;background:rgba(255,255,255,.18)}
.foot-list{top:1008px}
.foot-list li{list-style:none;position:relative;font-size:10.5px;line-height:22px;color:var(--white);padding-left:11px}
.foot-field{position:absolute;left:413px;width:161px;height:21px;background:var(--white);border-radius:2px;font-size:9px;color:#666;padding:5px 10px}
.foot-submit{left:515px;top:1093px;width:60px;height:20px;background:linear-gradient(#25a34b,#137a33);color:var(--white);font-size:11px;line-height:20px;text-align:center;border-radius:2px}
.contact{left:645px;top:1006px;color:var(--white);font-size:10px;line-height:18.5px}
.contact strong{display:block;font-size:12px;font-weight:400;line-height:14px;margin-bottom:7px}
.foot-social{left:647px;top:1105px;display:flex;gap:3px}
.foot-social span{width:18px;height:18px;border-radius:50%;background:var(--white)}
.foot-bottom-rule{left:0;top:1162px;width:910px;height:1px;background:rgba(255,255,255,.12)}
.copyright{left:74px;top:1176px;font-size:9px;color:rgba(255,255,255,.6)}
</style>
</head>
<body>
<div class="abs top-rule"></div>

<header>
  <div class="abs brand"><span class="brand-mark"></span><span class="brand-name">Bright Meadow</span></div>
  <div class="abs call"><div class="call-label">Call Us Now</div><div class="call-number">1300 555 274</div></div>
  <div class="abs socials"><span></span><span></span><span></span></div>
  <nav class="abs nav">
    <a>Home</a><a>About</a><a>Products</a><a>Services</a><a>Projects</a><a>Enquiry</a><a>Media</a><a>Contact</a>
  </nav>
</header>

<section>
  <div class="abs hero" role="img" aria-label="Blue sky with clouds over a large solar panel array"></div>
  <div class="abs hero-panels"></div>
  <h1 class="abs hero-title">Solar&nbsp; Photovoltaic</h1>
  <p class="abs hero-text">Phasellus felis dolor, scelerisque a, tempus eget, lobortis id, libero. Donec scelerisque leo ac risus. Praesent sit amet est. In dictum, dolor eu dictum porttitor</p>
  <div class="abs btn-learn">Learn More</div>
  <div class="abs dots"><span></span><span></span><span></span><span></span></div>

  <form class="abs enquiry">
    <div class="enquiry-head">Enquiry Form</div>
    <div class="field" style="top:49px">Name</div>
    <div class="field" style="top:79px">Phone Number</div>
    <div class="field" style="top:110px">How did you hear about us</div>
    <div class="field" style="top:141px;height:65px">Message</div>
    <div class="btn-orange" style="left:129px;top:211px;width:73px;height:24px;font-size:12px;line-height:24px">Submit</div>
  </form>
</section>

<section>
  <div class="abs card" style="left:80px"><h3>Perth Residential<br>Solar Power</h3><p>Nunc tempus felis vitae urna. Vivamus porttitor, g, purus nisi eleifend libero, a tempus libero lectus feugiat felis. Morbi diam mauris</p><span class="btn-green">READ MORE</span></div>
  <div class="abs card" style="left:272px"><h3>Perth Commercial<br>Solar Power</h3><p>Nunc tempus felis vitae urna. Vivamus porttitor, g, purus nisi eleifend libero, a tempus libero lectus feugiat felis. Morbi diam mauris</p><span class="btn-green">READ MORE</span></div>
  <div class="abs card" style="left:465px"><h3>Air Conditioning<br>WA</h3><p>Nunc tempus felis vitae urna. Vivamus porttitor, g, purus nisi eleifend libero, a tempus libero lectus feugiat felis. Morbi diam mauris</p><span class="btn-green">READ MORE</span></div>
  <div class="abs card" style="left:658px"><h3>Perth LED<br>Lighting</h3><p>Nunc tempus felis vitae urna. Vivamus porttitor, g, purus nisi eleifend libero, a tempus libero lectus feugiat felis. Morbi diam mauris</p><span class="btn-green">READ MORE</span></div>
</section>

<section>
  <h2 class="abs welcome-title" style="font-weight:400">Welcome to Our Website Mainpage..</h2>
  <p class="abs welcome-lead">Nunc tempus felis vitae urna Vivamus porttitor purus nisi eleifend libero, a tempus</p>
  <p class="abs welcome-text">Phasellus felis dolor, scelerisque a, tempus eget, lobortis id, libero. Donec scelerisque leo ac risus. Praesent sit amet est. In dictum, dolor eu dictum porttitor, enim felis viverra mi</p>
  <div class="abs photo" style="left:80px;top:785px;width:172px;height:112px" role="img" aria-label="Installer fitting solar panels on a rooftop"></div>
  <div class="abs benefits">
    <h4>Benefits &amp; Services Provide by Us:</h4>
    <ul><li>Phasellus felis dolor, scelerisque</li><li>Lobortis id libero.</li><li>Donec scelerisque leo ac risus.</li><li>In dictum dolor eu dictum porttitor</li></ul>
  </div>
  <h2 class="abs testimonials-title" style="font-weight:400">Testimonials</h2>
  <div class="abs video" role="img" aria-label="Video still of a customer and installer in front of a solar-powered home"></div>
  <svg class="abs play" width="36" height="36" viewBox="0 0 36 36"><circle cx="18" cy="18" r="17" fill="#222" stroke="#fff" stroke-width="2" opacity=".9"/><path d="M14 11 L26 18 L14 25 Z" fill="#fff"/></svg>
</section>

<footer>
  <div class="abs footer"></div>
  <h3 class="abs foot-head" style="left:85px;font-weight:400">Product Services</h3>
  <h3 class="abs foot-head" style="left:254px;font-weight:400">Membership</h3>
  <h3 class="abs foot-head" style="left:412px;font-weight:400">Request Quotation</h3>
  <h3 class="abs foot-head" style="left:644px;font-weight:400">Contact Info</h3>
  <div class="abs foot-rule" style="left:219px"></div>
  <div class="abs foot-rule" style="left:380px"></div>
  <div class="abs foot-rule" style="left:609px"></div>
  <ul class="abs foot-list" style="left:86px"><li>Celerisque&nbsp; tempus</li><li>Lobortis id libero</li><li>Donec scelerisque</li><li>Dolor eu dictum</li><li>Porttitor</li></ul>
  <ul class="abs foot-list" style="left:254px"><li>Nunc tempus felis</li><li>Vitae urna</li><li>Vivamus porttitor</li><li>Purus nisi eleifend</li><li>Libero a tempus</li></ul>
  <div class="foot-field" style="top:1009px">Name</div>
  <div class="foot-field" style="top:1037px">Email add</div>
  <div class="foot-field" style="top:1065px">Phone no.</div>
  <div class="abs foot-submit">Submit</div>
  <div class="abs contact">
    <strong>Bright Meadow Ltd</strong>
    210 Linden Row #4B<br>Westfield 20417 NY<br>Phone no. 1300 555 274<br>Email add: info@brightmeadow.co.uk
  </div>
  <div class="abs foot-social"><span></span><span></span><span></span><span></span></div>
  <div class="abs foot-bottom-rule"></div>
  <p class="abs copyright">© 2013 Company Name.&nbsp; All right reserved.&nbsp; Term of Use</p>
</footer>
</body>
</html>
```